Product label for herbal salves, lotions, soaps and tinctures

We need a very simple, clean and organic looking label that can be used for an ointment jar, a lotion bottle and a dropper bottle.
We have an existing logo (see attached). We like the colors white, olive green, gold and black. It needs to include product name as dominant and logo. It also needs to include an ingredient list, and usage statement. Include weight of product, distributed by, made in the USA, and QVX statement.
Example of what needs to be present:
Logo
Name: Tranquil Ease Blend
Used for: For Muscle Aches, Arthritis, Tendonitis, Headaches
To Use: For muscle aches, arthritis and tendonitis, massage into affected area. For tension headache apply to neck, temples and forehead.
Store in a cool and dry place, away from direct heat and sunlight.
Weight of product: 1.75
DIST. BY: Copper Brook Herbal
Made in the USA
This product is not intended to diagnose, treat, cure
or prevent any disease. Not regulated
by the QVX. Please consult your health care practitioner
before using product. Discontinue use if any adverse reaction occurs.
Ingredient list:
Wildcrafted Ingredients:
Ashwagandha Root, Peppermint Leaf, Hops Flowers, St. John’s Wort Herb, Arnica Flowers, Green Tea Leaf, Alfalfa Leaf, Dandelion Root, Burdock Root, Chickweed Herb, Chaparral Leaf, Yarrow Flowers, Boneset Herb, Moringa Leaf, Meadowsweet Herb, Nettle Leaf
Organic Ingredients:
Olive Oil, Aloe Leaf, Sweet Birch Bark, Helichrysum Flowers, Holy Basil Leaf, Borage Herb, Ginger Root, Angelica Root, White Willow Bark, Mustard Seed, Beeswax, Vitamin E, Essential Oils
Dimensions of Jar:
Circumference: 7 in.
Height: 1 in.

```html
<!DOCTYPE html>
<html lang="en">
<head>
<meta charset="utf-8">
<title>Tranquil Ease Blend – Label</title>
<link rel="stylesheet" href="https://fonts.googleapis.com/css2?family=Fira+Sans:wght@400;600&family=Playfair+Display:wght@700&display=swap">
<style>
  :root {
    --gold: #d4952a;
    --gold-line: #caa85a;
    --olive: #6b7431;
    --ink: #1d1d1b;
    --paper: #ffffff;
    --sprig: #e7ead8;
  }
  * { margin: 0; padding: 0; box-sizing: border-box; }
  html, body { width: 1200px; height: 632px; overflow: hidden; background: var(--paper); }
  body { font-family: "Fira Sans", sans-serif; color: var(--ink); }

  .label { position: absolute; left: 0; top: 228px; width: 1200px; height: 176px; }
  .label__rule { position: absolute; left: 0; top: 0; width: 1200px; height: 5px; background: var(--gold-line); }

  .botanical-band {
    position: absolute; left: 359px; top: 118px; width: 592px; height: 54px;
    background: linear-gradient(180deg, rgba(231,234,216,0) 0%, var(--sprig) 100%);
    opacity: .8;
  }

  .ingredients { position: absolute; left: 68px; top: 14px; width: 350px; font-size: 10px; line-height: 11.5px; }
  .ingredients__title { color: var(--olive); font-weight: 600; }
  .ingredients__group { color: var(--gold); font-weight: 600; }

  .distributor { position: absolute; left: 68px; top: 133px; font-size: 10px; line-height: 11.5px; }
  .distributor strong { font-weight: 600; }

  .storage {
    position: absolute; left: 163px; top: 134px; width: 170px; height: 28px;
    border: 1px solid var(--olive); padding: 2px 5px;
    font-size: 9.6px; line-height: 11.5px; font-weight: 600;
  }

  .brand { position: absolute; left: 440px; top: 34px; width: 150px; display: flex; align-items: center; gap: 6px; }
  .brand__dot { width: 12px; height: 12px; border-radius: 50%; background: var(--olive); flex: none; }
  .brand__name { font-family: "Fira Sans", sans-serif; font-weight: 600; color: var(--olive); font-size: 22px; line-height: 24px; }

  .product { position: absolute; left: 609px; top: 28px; }
  .product__name {
    font-family: "Playfair Display", serif; font-weight: 700; color: var(--gold);
    font-size: 33px; line-height: 33px; letter-spacing: 1.2px;
  }
  .product__uses {
    display: inline-block; margin-top: 6px; background: var(--olive); color: var(--paper);
    font-size: 10.5px; line-height: 13px; padding: 0 4px; width: 240px;
  }
  .product__weight { font-size: 10.5px; margin-top: 3px; padding-left: 3px; }

  .usage { position: absolute; left: 901px; top: 16px; width: 250px; font-size: 9.6px; line-height: 11.5px; }
  .usage__title { color: var(--olive); font-weight: 400; }
  .usage__steps { font-weight: 600; margin-bottom: 6px; }
</style>
</head>
<body>
  <section class="label">
    <div class="label__rule"></div>
    <div class="botanical-band" role="img" aria-label="Faint engraved olive branches and herb sprigs along the label base"></div>

    <div class="ingredients">
      <p class="ingredients__title">Ingredient list:</p>
      <p class="ingredients__group">Wildcrafted Ingredients:</p>
      <p>Ashwagandha Root, Peppermint Leaf, Hops Flowers, St. John’s Wort Herb, Arnica Flowers, Green Tea Leaf, Alfalfa Leaf, Dandelion Root, Burdock Root, Chickweed Herb, Chaparral Leaf, Yarrow Flowers, Boneset Herb, Moringa Leaf, Meadowsweet Herb, Nettle Leaf</p>
      <p class="ingredients__group">Organic Ingredients:</p>
      <p>Olive Oil, Aloe Leaf, Sweet Birch Bark, Helichrysum Flowers, Holy Basil Leaf, Borage Herb, Ginger Root, Angelica Root, White Willow Bark, Mustard Seed, Beeswax, Vitamin E, Essential Oils</p>
    </div>

    <div class="distributor">
      <p>Distributed by:</p>
      <p><strong>Copper Brook Herbal</strong></p>
      <p><strong>Made in the USA</strong></p>
    </div>

    <div class="storage">Store in a cool and dry place,<br>away from direct heat and sunlight.</div>

    <div class="brand">
      <span class="brand__dot"></span>
      <span class="brand__name">Copper Brook Herbal</span>
    </div>

    <div class="product">
      <h1 class="product__name">Tranquil Ease<br>Blend</h1>
      <p class="product__uses">Muscle Aches, Arthritis, Tendonitis, Headache</p>
      <p class="product__weight">1.75 oz</p>
    </div>

    <div class="usage">
      <p class="usage__title">How to Use :</p>
      <p class="usage__steps">For muscle aches, arthritis and tendonitis, massage into affected area.<br>For tension headache apply to neck, temples and forehead.</p>
      <p>This product is not intended to diagnose, treat, cure or prevent any disease.<br>Not regulated by the QVX.<br>Please consult your health care practitioner before using product.<br>Discontinue use if any adverse reaction occurs.</p>
    </div>
  </section>
</body>
</html>
```